Shopify Web-Page "Tiny-ThreadDays

We are building a new business in Switzerland offering premium sewing holiday camps for kids aged 9–14. In enclosed brief outlines our requirements for a complete Shopify homepage design and a multilingual logo creation.
Domains: tiny-threaddays.ch ; tiny-giornifilo.ch ; tiny-fadentage.ch

Project Overview
We are looking for:
1. A modern, fully designed Shopify homepage in English using standard Shopify content blocks (no custom coding), which we can later update ourselves. Supporting Multilanguage (EN, German, Italian).

2. A logo design that includes the brand identity and communicates our multilingual, creative, and child-focused positioning.

All details in enclosed

```html
<!DOCTYPE html>
<html lang="en">
<head>
<meta charset="utf-8">
<title>Tiny-ThreadDays – Premium Sewing Holiday Camps</title>
<link rel="stylesheet" href="https://fonts.googleapis.com/css2?family=Poppins:wght@400;500;600;700;800&display=swap">
<style>
:root{
  --cyan:#19aed6;
  --cyan-dark:#0f8fb5;
  --pink:#e8457f;
  --yellow:#f6c545;
  --green:#7cc36b;
  --orange:#f39a3d;
  --navy:#1d2944;
  --ink:#22263a;
  --muted:#6b7083;
  --soft-blue:#eaf6fb;
  --line:#e4e7ee;
  --white:#ffffff;
}
*{box-sizing:border-box;margin:0;padding:0}
html,body{width:1200px;height:4904px;overflow:hidden}
body{font-family:"Poppins",sans-serif;color:var(--ink);background:var(--white);font-size:13px;line-height:1.6;position:relative}
.section{position:absolute;left:0;width:1200px}
.eyebrow{font-size:12px;font-weight:700;letter-spacing:.08em;color:var(--cyan);text-transform:uppercase}
.title{font-size:26px;font-weight:800;text-transform:uppercase;line-height:1.25;color:var(--ink)}
.title em{font-style:normal;color:var(--pink);text-decoration:underline;text-decoration-color:var(--yellow);text-underline-offset:5px;text-decoration-thickness:3px}
.center{text-align:center}
.btn{display:inline-block;background:var(--cyan);color:var(--white);font-weight:600;font-size:12px;padding:10px 22px;border-radius:24px}
.btn-pink{background:var(--pink)}
.brand{font-weight:800;color:var(--pink);font-size:18px;display:flex;align-items:center;gap:8px}
.brand .dot{width:14px;height:14px;border-radius:50%;background:var(--yellow)}

/* header */
.site-header{top:0;height:70px;z-index:3;display:flex;align-items:center;padding:0 60px;justify-content:space-between}
.main-nav{display:flex;gap:28px;font-size:12px;font-weight:500}
.main-nav a{color:var(--ink);text-decoration:none}
.main-nav a.active{color:var(--pink);font-weight:700}
.header-tools{display:flex;align-items:center;gap:18px;font-size:12px}

/* hero */
.hero{top:0;height:430px;background:linear-gradient(100deg,#f4f8fb 0%,#f1f4f6 38%,#d9e3ea 60%,#c6d3db 100%)}
.hero-photo{position:absolute;right:0;top:0;width:720px;height:430px;background:linear-gradient(90deg,rgba(241,244,246,0) 0%,#d6c7bd 30%,#c9b8ad 70%,#bfb0a6 100%)}
.hero-copy{position:absolute;left:60px;top:150px;width:420px}
.hero-copy h1{font-size:38px;font-weight:800;line-height:1.15;color:var(--cyan);text-transform:uppercase}
.hero-copy h1 span{color:var(--pink)}
.hero-copy p{margin:14px 0 18px;font-size:13px;color:var(--ink)}
.hero-proof{margin-top:20px;display:flex;align-items:center;gap:10px;font-size:12px;font-weight:500}
.hero-proof .faces{width:54px;height:22px;border-radius:12px;background:linear-gradient(90deg,#f3c7a6,#d9a27f)}
.hero-wave{position:absolute;left:0;bottom:-1px;width:1200px;height:60px}

/* about */
.about{top:440px;height:600px}
.about-collage{position:absolute;left:80px;top:40px;width:480px;height:480px}
.about-collage .ring{position:absolute;left:120px;top:110px;width:240px;height:240px;border-radius:50%;background:conic-gradient(var(--pink) 0 25%,var(--yellow) 0 50%,var(--cyan) 0 75%,var(--green) 0)}
.about-collage .ph{position:absolute;border-radius:14px;background:linear-gradient(135deg,#e8d6c6,#c8ae98)}
.about-copy{position:absolute;left:610px;top:120px;width:500px}
.about-copy .title{margin:8px 0 16px}
.about-copy p{color:var(--muted);margin-bottom:12px;font-size:12.5px}
.team{display:flex;gap:50px;margin-top:22px}
.member{display:flex;align-items:center;gap:12px}
.avatar{width:46px;height:46px;border-radius:50%;background:linear-gradient(135deg,#d9b49a,#9f7a65)}
.member b{display:block;font-size:14px}
.member small{color:var(--muted);font-size:11px}

/* how it works */
.how{top:1080px;height:500px;background:var(--soft-blue)}
.wave-top{position:absolute;left:0;top:-1px;width:1200px;height:50px}
.how .head{position:absolute;top:80px;width:100%}
.steps{position:absolute;top:170px;left:110px;display:flex;gap:22px}
.step{width:176px;height:220px;background:var(--white);border-radius:16px;padding:20px 16px;position:relative;box-shadow:0 6px 18px rgba(30,60,100,.08)}
.step .num{position:absolute;right:14px;top:10px;font-size:36px;font-weight:800;color:#eef1f5}
.step .ic{width:44px;height:44px;border-radius:50%;display:flex;align-items:center;justify-content:center}
.step h4{font-size:13px;font-weight:700;margin:14px 0 6px}
.step p{font-size:11px;color:var(--muted);line-height:1.5}

/* why */
.why{top:1600px;height:700px}
.why .head{position:absolute;top:60px;width:100%}
.emblem{position:absolute;left:480px;top:230px;width:240px;height:240px;border-radius:50%;border:3px dashed var(--cyan);display:flex;align-items:center;justify-content:center}
.emblem .inner{width:200px;height:200px;border-radius:50%;background:var(--white);box-shadow:0 8px 24px rgba(0,0,0,.08);display:flex;align-items:center;justify-content:center;font-weight:800;color:var(--pink);font-size:20px}
.feature{position:absolute;width:280px;display:flex;align-items:center;gap:14px;font-size:13px;font-weight:500}
.feature.left{flex-direction:row-reverse;text-align:right}
.feature .ic{flex:none;width:54px;height:54px;border-radius:50%;display:flex;align-items:center;justify-content:center}

/* camps */
.camps{top:2320px;height:680px}
.camps .head{position:absolute;top:60px;width:100%}
.camp-grid{position:absolute;top:170px;left:70px;display:flex;gap:20px}
.camp{width:250px;border:1px solid var(--line);border-radius:14px;overflow:hidden;background:var(--white)}
.camp .ph{height:150px}
.camp .body{padding:14px}
.camp h4{font-size:14px;font-weight:700}
.camp p{font-size:11px;color:var(--muted);margin:6px 0 10px;line-height:1.5}
.meta{display:grid;grid-template-columns:1fr 1fr;gap:4px 10px;font-size:10.5px;border-top:1px solid var(--line);padding-top:8px}
.meta b{font-weight:600}
.camps .cta{position:absolute;top:590px;width:100%;text-align:center}

/* banner */
.banner{top:3030px;height:470px}
.banner-bg{position:absolute;left:0;top:0;width:1200px;height:470px}
.banner .copy{position:absolute;top:170px;width:100%;color:var(--white);text-align:center}
.banner h2{font-size:36px;font-weight:800;text-transform:uppercase}
.banner p{margin:10px auto 20px;width:560px;font-size:13px}
.btn-light{background:var(--white);color:var(--cyan)}

/* faq */
.faq{top:3520px;height:950px}
.faq .head{position:absolute;top:10px;width:100%}
.faq-list{position:absolute;top:110px;left:200px;width:800px}
.qa{border:1px solid var(--line);border-radius:8px;margin-bottom:11px;padding:16px 20px;font-size:13px;font-weight:500;display:flex;justify-content:space-between;align-items:center}
.qa.open{display:block;box-shadow:0 6px 18px rgba(0,0,0,.06)}
.qa.open .q{display:flex;justify-content:space-between}
.qa.open p{font-size:11.5px;color:var(--muted);font-weight:400;margin-top:10px}
.to-top{position:absolute;right:195px;top:880px;width:38px;height:38px;border-radius:50%;background:var(--pink);display:flex;align-items:center;justify-content:center}

/* footer */
.site-footer{top:4470px;height:434px;background:var(--navy);color:#cfd5e2}
.foot-cols{position:absolute;top:70px;left:90px;display:flex;gap:80px}
.foot-brand .brand{font-size:24px}
.socials{display:flex;gap:8px;margin-top:70px;align-items:center;font-size:12px}
.socials i{width:22px;height:22px;border-radius:50%;background:var(--cyan);display:block}
.foot-col h5{color:var(--yellow);font-size:14px;font-weight:700;margin-bottom:14px}
.foot-col li{list-style:none;font-size:12px;margin-bottom:8px}
.contact li{display:flex;gap:10px;align-items:flex-start;width:220px}
.contact .pi{flex:none;width:22px;height:22px;border-radius:50%;background:var(--cyan)}
.newsletter p{font-size:12px;width:260px}
.sub{margin-top:16px;width:270px;height:40px;border-radius:22px;background:var(--white);position:relative;padding:10px 16px;color:#9aa0b0;font-size:12px}
.sub span{position:absolute;right:4px;top:4px;width:32px;height:32px;border-radius:50%;background:var(--pink)}
.copyright{position:absolute;bottom:0;width:100%;border-top:1px solid #34405c;text-align:center;font-size:11px;padding:16px 0}
</style>
</head>
<body>

<section class="section hero">
  <div class="hero-photo" role="img" aria-label="Smiling children holding fabric in a bright sewing studio"></div>
  <div class="hero-copy">
    <h1>Premium Sewing <span>Holiday Camps</span> for Kids 9–14</h1>
    <p>Creative fun in Zurich – Multilingual and inspiring! Learn sewing, build confidence, and create unique fashion pieces in our small group camps.</p>
    <span class="btn">View Upcoming Camps ›</span>
    <div class="hero-proof"><span class="faces"></span>Join 300+ happy campers!</div>
  </div>
  <svg class="hero-wave" viewBox="0 0 1200 60" preserveAspectRatio="none"><path d="M0 40 C300 0 600 70 900 30 C1050 10 1150 30 1200 20 L1200 60 L0 60Z" fill="#fff"/></svg>
</section>

<header class="section site-header">
  <div class="brand"><span class="dot"></span>Tiny-ThreadDays</div>
  <nav class="main-nav"><a class="active">Home</a><a>About Us</a><a>Camps</a><a>How it Works</a><a>FAQs</a><a>Contact</a></nav>
  <div class="header-tools"><span>English ▾</span><span class="btn btn-pink">Contact Us</span></div>
</header>

<section class="section about">
  <div class="about-collage">
    <div class="ring"></div>
    <div class="ph" role="img" aria-label="Girl sewing at a machine" style="left:20px;top:10px;width:220px;height:200px"></div>
    <div class="ph" role="img" aria-label="Hands cutting fabric" style="left:260px;top:60px;width:200px;height:170px"></div>
    <div class="ph" role="img" aria-label="Children pinning a pattern" style="left:60px;top:250px;width:200px;height:200px"></div>
    <div class="ph" role="img" aria-label="Finished garment on display" style="left:280px;top:260px;width:180px;height:180px"></div>
  </div>
  <div class="about-copy">
    <div class="eyebrow">About our camps</div>
    <h2 class="title">Learning with fun &amp; <em>structure</em></h2>
    <p>At Tiny-ThreadDays, we believe in nurturing creativity while having fun. Our experienced instructors create a safe, inspiring environment where children can explore their creative potential.</p>
    <p>With over 15 years of experience in teaching children sewing, tailoring, and design, we guide young talents through a creative week of vacation – with real results, self-sewn pieces, new friends, and lots of pride.</p>
    <p>At the last day, the children show off their success: their own sewn unique pieces, in a sympathetic fashion show.</p>
    <div class="team">
      <div class="member"><span class="avatar" role="img" aria-label="Portrait of instructor Mara"></span><div><b>Mara</b><small>Sewing Expert</small></div></div>
      <div class="member"><span class="avatar" role="img" aria-label="Portrait of instructor Lena"></span><div><b>Lena</b><small>Design Specialist</small></div></div>
    </div>
  </div>
</section>

<section class="section how">
  <svg class="wave-top" viewBox="0 0 1200 50" preserveAspectRatio="none"><path d="M0 0 H1200 V20 C900 50 600 0 300 30 C150 45 50 30 0 25Z" fill="#fff"/></svg>
  <div class="head center">
    <div class="eyebrow">How our camps work</div>
    <h2 class="title" style="margin-top:6px">Creative holiday camps for young <em>sewing champs!</em></h2>
  </div>
  <div class="steps">
    <div class="step"><span class="num">01</span><div class="ic" style="background:#fde3ec"><svg width="22" height="22" viewBox="0 0 24 24" fill="none" stroke="#e8457f" stroke-width="2"><rect x="4" y="4" width="16" height="16" rx="3"/><path d="M8 10h8M8 14h5"/></svg></div><h4>Project Selection</h4><p>Your child chooses their own model based on previously produced clothing items and sewing patterns.</p></div>
    <div class="step"><span class="num">02</span><div class="ic" style="background:#fff4d6"><svg width="22" height="22" viewBox="0 0 24 24" fill="none" stroke="#f39a3d" stroke-width="2"><path d="M4 18 L12 4 L20 18Z"/></svg></div><h4>Fabric selection</h4><p>High-quality fabrics are available.</p></div>
    <div class="step"><span class="num">03</span><div class="ic" style="background:#dff3fa"><svg width="22" height="22" viewBox="0 0 24 24" fill="none" stroke="#19aed6" stroke-width="2"><rect x="3" y="10" width="18" height="8" rx="2"/><path d="M7 10V6h10v4"/></svg></div><h4>Sewing machine</h4><p>Learn how to use a sewing machine.</p></div>
    <div class="step"><span class="num">04</span><div class="ic" style="background:#e5f5e0"><svg width="22" height="22" viewBox="0 0 24 24" fill="none" stroke="#7cc36b" stroke-width="2"><path d="M5 19 L19 5M14 5h5v5"/></svg></div><h4>Sewing &amp; refining</h4><p>Step by step to the goal with professional guidance!</p></div>
    <div class="step"><span class="num">05</span><div class="ic" style="background:#fde3ec"><svg width="22" height="22" viewBox="0 0 24 24" fill="none" stroke="#e8457f" stroke-width="2"><path d="M12 3l2.6 5.6 6 .7-4.5 4.1 1.2 6L12 16.5 6.7 19.4l1.2-6L3.4 9.3l6-.7Z"/></svg></div><h4>Showtime!</h4><p>Fashion show in proud style at the end of the week!</p></div>
  </div>
</section>

<section class="section why">
  <div class="head center">
    <div class="eyebrow">Why parents choose us</div>
    <h2 class="title" style="margin-top:6px">Why families love Tiny-ThreadDays <em>camps</em></h2>
  </div>
  <div class="emblem"><div class="inner">Tiny-ThreadDays</div></div>
  <div class="feature left" style="left:170px;top:220px"><span class="ic" style="background:var(--yellow)"><svg width="24" height="24" viewBox="0 0 24 24" fill="none" stroke="#fff" stroke-width="2"><circle cx="8" cy="9" r="3"/><circle cx="16" cy="9" r="3"/><path d="M3 19c1-4 9-4 10 0M11 19c1-4 9-4 10 0"/></svg></span>Small groups &amp; personalized attention</div>
  <div class="feature left" style="left:170px;top:330px"><span class="ic" style="background:var(--green)"><svg width="24" height="24" viewBox="0 0 24 24" fill="none" stroke="#fff" stroke-width="2"><path d="M4 6h9M8 4v2M6 6c0 4 4 7 6 8M12 20l4-9 4 9M13.5 17h5"/></svg></span>Multilingual supervision (DE / EN / IT)</div>
  <div class="feature left" style="left:170px;top:440px"><span class="ic" style="background:var(--pink)"><svg width="24" height="24" viewBox="0 0 24 24" fill="none" stroke="#fff" stroke-width="2"><path d="M12 21s-7-6.5-7-12a7 7 0 0 1 14 0c0 5.5-7 12-7 12z"/><circle cx="12" cy="9" r="2.5"/></svg></span>Pick-up Service from the Main Station</div>
  <div class="feature" style="left:750px;top:220px"><span class="ic" style="background:var(--cyan)"><svg width="24" height="24" viewBox="0 0 24 24" fill="none" stroke="#fff" stroke-width="2"><path d="M9 18h6M10 21h4M12 3a6 6 0 0 0-3 11v2h6v-2a6 6 0 0 0-3-11z"/></svg></span>Encouragement of creativity, self-confidence, and fine motor skills</div>
  <div class="feature" style="left:750px;top:330px"><span class="ic" style="background:var(--pink)"><svg width="24" height="24" viewBox="0 0 24 24" fill="none" stroke="#fff" stroke-width="2"><path d="M12 3l8 3v6c0 5-4 8-8 9-4-1-8-4-8-9V6z"/><path d="M8.5 12l2.5 2.5 4.5-5"/></svg></span>Safe, loving environment in Zurich, various places easy to reach</div>
  <div class="feature" style="left:750px;top:440px"><span class="ic" style="background:var(--orange)"><svg width="24" height="24" viewBox="0 0 24 24" fill="none" stroke="#fff" stroke-width="2"><rect x="3" y="10" width="18" height="8" rx="2"/><path d="M7 10V6h10v4"/></svg></span>High-quality fabrics &amp; top-quality sewing machines</div>
</section>

<section class="section camps">
  <div class="head center">
    <div class="eyebrow">Our upcoming camps</div>
    <h2 class="title" style="margin-top:6px">Multilingual creativity, made just <em>for kids</em></h2>
  </div>
  <div class="camp-grid">
    <div class="camp"><div class="ph" role="img" aria-label="Children sewing spring outfits" style="background:linear-gradient(135deg,#f1d9c8,#c9a58c)"></div><div class="body"><h4>Spring Camp</h4><p>Join us for a creative week of spring-themed fun! Children will learn sewing basics and create their own spring-inspired projects.</p><div class="meta"><span><b>Age:</b> 09 to 14</span><span><b>Total:</b> 200 Kids</span><span><b>Date:</b> 21 Oct 2025</span><span><b>Duration:</b> 06 Days</span></div></div></div>
    <div class="camp"><div class="ph" role="img" aria-label="Kids measuring fabric for summer pieces" style="background:linear-gradient(135deg,#e6dccf,#b9a591)"></div><div class="body"><h4>Summer Camp</h4><p>Our popular summer program where kids design and create their own summer wardrobe items in a fun, supportive environment.</p><div class="meta"><span><b>Age:</b> 09 to 14</span><span><b>Total:</b> 200 Kids</span><span><b>Date:</b> 07 Jul 2025</span><span><b>Duration:</b> 06 Days</span></div></div></div>
    <div class="camp"><div class="ph" role="img" aria-label="Group working on autumn accessories" style="background:linear-gradient(135deg,#ead3c0,#c49a7c)"></div><div class="body"><h4>Autumn Camp</h4><p>Get ready for cooler weather by creating cozy autumn accessories and clothing items in this creative camp.</p><div class="meta"><span><b>Age:</b> 09 to 14</span><span><b>Total:</b> 200 Kids</span><span><b>Date:</b> 21 Oct 2025</span><span><b>Duration:</b> 06 Days</span></div></div></div>
    <div class="camp"><div class="ph" role="img" aria-label="Girls sewing warm winter garments" style="background:linear-gradient(135deg,#dfd6d0,#a99488)"></div><div class="body"><h4>Winter Camp</h4><p>Get ready for cooler weather by creating cozy winter accessories and clothing items in this creative camp.</p><div class="meta"><span><b>Age:</b> 09 to 14</span><span><b>Total:</b> 200 Kids</span><span><b>Date:</b> 21 Oct 2025</span><span><b>Duration:</b> 06 Days</span></div></div></div>
  </div>
  <div class="cta"><span class="btn btn-pink">View All Camps ›</span></div>
</section>

<section class="section banner">
  <svg class="banner-bg" viewBox="0 0 1200 470" preserveAspectRatio="none"><path d="M0 70 C300 0 600 110 900 50 C1050 20 1150 40 1200 30 V420 C900 480 600 400 300 450 C150 470 50 450 0 440Z" fill="#19aed6"/></svg>
  <div class="copy">
    <h2>Ready for a creative adventure?</h2>
    <p>Spaces are limited to 6 children per camp to ensure personalized attention. Book now to secure your child's spot!</p>
    <span class="btn btn-light">View All Camps ›</span>
  </div>
</section>

<section class="section faq">
  <div class="head center">
    <div class="eyebrow">Frequently asked questions</div>
    <h2 class="title" style="margin-top:6px">Everything you need to know about <em>our camps</em></h2>
  </div>
  <div class="faq-list">
    <div class="qa open"><div class="q"><span>Does my child need any prior knowledge?</span><span>⌃</span></div><p>We welcome children aged 9–14 years. The age range ensures that participants have the fine motor skills needed for sewing while still being excited about creative projects.</p></div>
    <div class="qa"><span>How does the pick-up service work?</span><span>⌄</span></div>
    <div class="qa"><span>How many items of clothing are produced?</span><span>⌄</span></div>
    <div class="qa"><span>What should my child bring to camp?</span><span>⌄</span></div>
    <div class="qa"><span>What are the camp hours?</span><span>⌄</span></div>
    <div class="qa"><span>We offer pick-up from Zurich Main Station at times. Parents can arrange this during booking</span><span>⌄</span></div>
    <div class="qa"><span>What is your cancellation policy?</span><span>⌄</span></div>
    <div class="qa"><span>How many items of clothing are produced?</span><span>⌄</span></div>
    <div class="qa"><span>Each child completes their own unique clothing item during the week</span><span>⌄</span></div>
    <div class="qa"><span>What safety measures are in place?</span><span>⌄</span></div>
  </div>
  <div class="to-top"><svg width="16" height="16" viewBox="0 0 24 24" fill="none" stroke="#fff" stroke-width="3"><path d="M6 15l6-6 6 6"/></svg></div>
</section>

<footer class="section site-footer">
  <div class="foot-cols">
    <div class="foot-brand"><div class="brand"><span class="dot"></span>Tiny-ThreadDays</div><div class="socials">Follow Us: <i></i><i></i><i></i></div></div>
    <div class="foot-col"><h5>Quick Links</h5><ul><li>Home</li><li>About Us</li><li>Camps</li><li>How It Works</li><li>Contact</li></ul></div>
    <div class="foot-col contact"><h5>Contact Us</h5><ul><li><span class="pi"></span>A-123, There are many variations Zurich, Switzerland</li><li><span class="pi"></span>Phone: (123) 456 7890</li><li><span class="pi"></span>info@tiny-threaddays.ch</li></ul></div>
    <div class="foot-col newsletter"><h5>Subscribe to newsletter</h5><p>Latest updates, exclusive content, and special offers? Subscribe to our newsletter!</p><div class="sub">Your Email<span></span></div></div>
  </div>
  <div class="copyright">© 2025 Tiny-ThreadDays. All Rights Reserved</div>
</footer>

</body>
</html>
```